Local fast-growing company in the service sector

We are looking for a modern business card design, which should also appear on our letterheads

Target Market(s)

Private and industrial sectors

Contact Information for Business Card

Vorname Name
Kellberger Str. 18
70999 Lindenfeld
Tel.: 07146-839214-0
Name@agentur-kvtl.de

Colors
9d9d9d
919191
aaaaaa

Requirements
Must have
• The logo (file) in silver

```html
<!DOCTYPE html>
<html lang="de">
<head>
<meta charset="utf-8">
<title>KVTL Visitenkarte</title>
<link href="https://fonts.googleapis.com/css2?family=Work+Sans:wght@400;600;700&family=Arimo:wght@400;700&display=swap" rel="stylesheet">
<style>
  :root {
    --page: #1b1b1d;
    --card: #323335;
    --card-edge: #2a2b2d;
    --silver: #aaaaaa;
    --silver-mid: #9d9d9d;
    --silver-dark: #919191;
    --ink: #111112;
  }
  * { box-sizing: border-box; margin: 0; padding: 0; }
  html, body { width: 1200px; height: 900px; overflow: hidden; }
  body {
    background: var(--page);
    font-family: "Work Sans", sans-serif;
    position: relative;
  }
  .card {
    position: absolute;
    left: 190px;
    width: 820px;
    height: 400px;
    background: linear-gradient(135deg, #3a3b3d 0%, var(--card) 55%, var(--card-edge) 100%);
    box-shadow: 0 14px 30px rgba(0,0,0,.55);
    overflow: hidden;
  }
  .card--front { top: 35px; }
  .card--back { top: 465px; }

  .brand {
    position: absolute;
    display: flex;
    align-items: center;
    gap: 14px;
    color: var(--silver);
  }
  .brand__mark {
    width: 34px; height: 34px;
    background: var(--silver);
  }
  .brand__name {
    font-family: "Work Sans", sans-serif;
    font-weight: 700;
    font-size: 58px;
    letter-spacing: 1px;
    line-height: 1;
  }
  .card--front .brand { right: 70px; bottom: 70px; }
  .card--back .brand { left: 470px; top: 92px; }

  .name-band {
    position: absolute;
    left: 0; top: 38px;
    width: 430px; height: 96px;
    background: var(--silver);
    padding: 24px 0 0 44px;
    color: var(--ink);
  }
  .name-band__name {
    font-family: "Arimo", sans-serif;
    font-weight: 700;
    font-size: 30px;
    line-height: 1;
  }
  .name-band__role {
    font-family: "Arimo", sans-serif;
    font-size: 14px;
    letter-spacing: .5px;
    margin-top: 3px;
  }

  .contact {
    position: absolute;
    left: 44px; top: 228px;
    list-style: none;
    color: var(--silver-mid);
    font-size: 20px;
    letter-spacing: .5px;
  }
  .contact li {
    display: flex;
    align-items: center;
    gap: 14px;
    height: 30px;
  }
  .contact svg { width: 14px; height: 14px; fill: none; stroke: var(--silver-dark); stroke-width: 1.6; }

  .address {
    position: absolute;
    right: 60px; bottom: 44px;
    color: var(--silver-mid);
    font-size: 20px;
    font-style: normal;
    line-height: 1.3;
    letter-spacing: .5px;
  }
</style>
</head>
<body>

  <section class="card card--front" aria-label="Vorderseite">
    <div class="brand">
      <span class="brand__mark"></span>
      <span class="brand__name">KVTL</span>
    </div>
  </section>

  <section class="card card--back" aria-label="Rückseite">
    <div class="name-band">
      <p class="name-band__name">JONAS WEBER</p>
      <p class="name-band__role">DIRECTOR</p>
    </div>

    <div class="brand">
      <span class="brand__mark"></span>
      <span class="brand__name">KVTL</span>
    </div>

    <ul class="contact">
      <li>
        <svg viewBox="0 0 14 14" aria-hidden="true"><path d="M3 1.5l2 2.5-1.2 1.5c.8 1.8 2 3 3.7 3.7L9 8l2.5 2-1 2c-5 0-9-4-9-9z"/></svg>
        07146-839214-0
      </li>
      <li>
        <svg viewBox="0 0 14 14" aria-hidden="true"><rect x="3.5" y="1" width="7" height="12" rx="1.2"/><path d="M6 11h2"/></svg>
        0152-48361907
      </li>
      <li>
        <svg viewBox="0 0 14 14" aria-hidden="true"><rect x="1" y="5" width="12" height="7"/><path d="M3.5 5V1.5h7V5M3.5 8.5h7"/></svg>
        07146-839214-9
      </li>
      <li>
        <svg viewBox="0 0 14 14" aria-hidden="true"><rect x="1" y="3" width="12" height="8.5"/><path d="M1 3l6 5 6-5"/></svg>
        Name@agentur-kvtl.de
      </li>
    </ul>

    <address class="address">
      Kellberger Str. 18<br>
      70999 Lindenfeld
    </address>
  </section>

</body>
</html>
```